Flat bootstrap design for existing site

I'm looking for a modern flat design based around an existing logo. This has to be a custom design (no external templates), and implemented into a bootstrap framework.

The logo is attached as 2 versions - choose whichever you want, that flows better with whatever design you choose.

Added screenshots of the existing site (currently using the default bootstrap layouts). Please make your designs around those pages in the screenshots (i.e. the homepage only has the postal code input and the header). The active page has 3 screenshots, because I wanted to illustrate the other states that would be visible (in the table rows).

This is a moving/junk removal website, just for some context.

Here's some example websites (flat designs) that I like, just to give you an idea of what I'm after.

https://www.plimvora.com/
https://dacklow.com/
https://trevanu.com/
https://quobrintal.com/en/

Coding

Coded - Design and coding required

Number of Pages Required

5+ page

Colors

Designer to choose colors to be used in the design.

Requirements
Must have
• It must be a modern/simple flat design, that is built around the existing logo (attached).
• It has to be implemented using bootstrap.

```html
<!DOCTYPE html>
<html lang="en">
<head>
<meta charset="utf-8">
<title>Haulvex – Booking Details</title>
<link href="https://fonts.googleapis.com/css2?family=Montserrat:wght@400;500;600;700&display=swap" rel="stylesheet">
<style>
:root{
  --brand:#4ac8f4;
  --brand-dark:#0a7eaa;
  --ink:#111;
  --muted:#666;
  --line:#e6e6e6;
  --panel:#fafafa;
  --white:#fff;
}
*{box-sizing:border-box;margin:0;padding:0}
html,body{width:1200px;height:1178px;overflow:hidden;font-family:"Montserrat",sans-serif;color:var(--ink);background:var(--white)}
.site-header{position:absolute;left:0;top:0;width:1200px;height:85px;background:var(--white)}
.brand{position:absolute;left:90px;top:24px;display:flex;align-items:center;gap:8px;font-size:30px;font-weight:700;color:var(--brand);letter-spacing:1px}
.brand-dot{width:14px;height:14px;background:var(--brand);border-radius:50%}
.nav-link{position:absolute;top:35px;font-size:13px;font-weight:600;color:var(--ink)}
.nav-book{left:467px}
.nav-how{left:550px}
.btn-driver{position:absolute;left:690px;top:21px;width:178px;height:43px;border-radius:22px;background:var(--brand);color:var(--white);font-size:13px;font-weight:600;display:flex;align-items:center;justify-content:center}
.user-pill{position:absolute;left:880px;top:20px;width:170px;height:45px;border:1px solid #eee;border-radius:23px;display:flex;align-items:center;padding-left:3px;gap:9px;font-size:11px;color:#333}
.user-avatar{width:37px;height:37px;border-radius:50%;background:linear-gradient(135deg,#8a9a6a,#c9a585)}
.user-pill svg{margin-left:4px}
.stage{position:absolute;left:0;top:85px;width:1200px;height:1022px;background:var(--brand)}
.card{position:absolute;left:90px;top:141px;width:1020px;height:942px;background:var(--panel)}
.card-head{height:62px;background:var(--white);padding:22px 32px;font-size:17px;font-weight:500;color:#555}
.field-label{position:absolute;font-size:11px;font-weight:600;color:#666}
.field{position:absolute;background:var(--white);display:flex;align-items:center;font-size:12px;color:#333}
.field-package{left:18px;top:130px;width:476px;height:53px;padding:0 18px 0 14px;gap:10px}
.field-package .caret{margin-left:auto}
.field-time{left:523px;top:130px;width:477px;height:53px;padding:0 10px;gap:10px}
.field-desc{left:18px;top:221px;width:982px;height:104px;align-items:flex-start;padding:18px 20px}
.btn-update{position:absolute;left:25px;top:356px;width:179px;height:43px;border-radius:22px;background:var(--brand);color:var(--white);font-size:13px;font-weight:600;display:flex;align-items:center;justify-content:center}
.section-title{position:absolute;left:24px;top:464px;font-size:17px;font-weight:600}
.bookings{position:absolute;left:23px;top:511px;width:979px;border-collapse:collapse;background:var(--panel)}
.bookings th,.bookings td{border:1px solid var(--line);text-align:left;font-size:12px}
.bookings th{height:56px;font-weight:700;font-size:13px;padding-left:19px}
.bookings th.col-time{padding-left:33px}
.bookings td{height:73px;padding-left:19px}
.col-name{width:181px}.col-dist{width:182px}
.driver{display:flex;align-items:center;gap:12px;font-size:13px;color:#333}
.driver-photo{width:44px;height:44px;border-radius:50%;background:linear-gradient(135deg,#4a5a6a,#c7b7a4)}
.time-cell{display:flex;align-items:center;justify-content:space-between;padding-right:34px}
.time-cell .dash{margin-left:96px}
.status{width:119px;height:29px;background:var(--brand-dark);color:var(--white);font-size:11px;font-weight:600;display:flex;align-items:center;justify-content:center}
.btn-more{position:absolute;left:433px;top:878px;width:154px;height:40px;border:3px solid #b6e9fb;border-radius:20px;font-size:11px;font-weight:600;color:#555;display:flex;align-items:center;justify-content:center}
.site-footer{position:absolute;left:0;top:1107px;width:1200px;height:71px;display:flex;align-items:center;justify-content:center;font-size:13px;color:#666;padding-left:0}
</style>
</head>
<body>
<header class="site-header">
  <div class="brand"><span class="brand-dot"></span>Haulvex</div>
  <span class="nav-link nav-book">BOOK</span>
  <span class="nav-link nav-how">HOW IT WORKS</span>
  <span class="btn-driver">BECOME A DRIVER</span>
  <div class="user-pill">
    <span class="user-avatar" role="img" aria-label="User profile photo"></span>
    <span>george@haulvex.in</span>
    <svg width="8" height="5" viewBox="0 0 8 5"><path d="M1 1l3 3 3-3" fill="none" stroke="#ccc" stroke-width="1"/></svg>
  </div>
</header>

<main class="stage">
  <section class="card" style="top:56px">
    <div class="card-head">Booking Details</div>

    <span class="field-label" style="left:18px;top:105px">Package Selected</span>
    <span class="field-label" style="left:523px;top:105px">Pick-Up Time Selected</span>

    <div class="field field-package">
      <svg width="18" height="16" viewBox="0 0 18 16"><rect x="1" y="4" width="16" height="11" rx="1" fill="#ddd"/><rect x="6" y="1" width="6" height="4" fill="none" stroke="#ddd" stroke-width="1.5"/></svg>
      Package 1
      <svg class="caret" width="11" height="7" viewBox="0 0 11 7"><path d="M1 1l4.5 4.5L10 1" fill="none" stroke="#222" stroke-width="2"/></svg>
    </div>

    <div class="field field-time">
      <svg width="16" height="16" viewBox="0 0 16 16"><rect x="1" y="2" width="14" height="13" fill="none" stroke="#ccc"/><path d="M1 6h14M5 9h1M8 9h1M11 9h1M5 12h1M8 12h1M11 12h1" stroke="#ccc"/></svg>
      <span>July 7th 2017&nbsp;&nbsp;&nbsp; Time&nbsp; 12:00 AM</span>
    </div>

    <span class="field-label" style="left:18px;top:204px">Description</span>
    <div class="field field-desc">1 Large Stove</div>

    <span class="btn-update">UPDATE</span>

    <h2 class="section-title">Booking Details</h2>

    <table class="bookings">
      <tr><th class="col-name">Name</th><th class="col-dist">Distance (Km)</th><th class="col-time">Agreed Pick Up Time</th></tr>
      <tr><td><div class="driver"><span class="driver-photo" role="img" aria-label="Driver photo"></span>Dario Penn</div></td><td>4.04 Km Away</td><td><div class="time-cell"><span class="dash">_</span><span class="status">Pending</span></div></td></tr>
      <tr><td><div class="driver"><span class="driver-photo" role="img" aria-label="Driver photo" style="background:linear-gradient(135deg,#6fa3c9,#e3d3c0)"></span>Teo Walsh</div></td><td>4.04 Km Away</td><td><div class="time-cell"><span class="dash">_</span><span class="status">Pending</span></div></td></tr>
      <tr><td><div class="driver"><span class="driver-photo" role="img" aria-label="Driver photo" style="background:linear-gradient(135deg,#8c7a5c,#b9a891)"></span>Arlo Finch</div></td><td>4.04 Km Away</td><td><div class="time-cell"><span class="dash">_</span><span class="status">Pending</span></div></td></tr>
      <tr><td><div class="driver"><span class="driver-photo" role="img" aria-label="Driver photo" style="background:linear-gradient(135deg,#5a4b44,#8fa2a8)"></span>Bram Keller</div></td><td>4.04 Km Away</td><td><div class="time-cell"><span class="dash">_</span><span class="status">Pending</span></div></td></tr>
    </table>

    <span class="btn-more">VIEW MORE DETAILS</span>
  </section>
</main>

<footer class="site-footer">© 2017 Company Name &nbsp;|&nbsp;All Rights Reserved</footer>
</body>
</html>
```